Company Profile for Academic and Study Abroad Services

I am looking for Power Point Design for company Profile . the company is academic and study abroad services. you can visit the website which is www.korvapath.ae . the colour i prefer is Dark Blue + White + Black . you can find all the content for power point and logo and some picture i need you to add it.

Target Market(s)

Students who wants to study abroad. Universities . Learning centre.

Industry/Entity Type

Education

Font styles to use
Serif
Sans Serif

Colors
0555a3
ffffff
000000
aaaaaa

Requirements
Must have
• Must Have Images for each slides.
Nice to have
• infographic. Images related to the study abroad

```html
<!DOCTYPE html>
<html lang="en">
<head>
<meta charset="utf-8">
<title>Korva Path — Company Profile Slides</title>
<link rel="stylesheet" href="https://fonts.googleapis.com/css2?family=Open+Sans:wght@400;600;700&display=swap">
<style>
  :root {
    --stage: #8c8c8c;
    --paper: #ffffff;
    --royal: #0c0ea4;
    --header-grey: #9a9c9e;
    --ink-1: #262b31;
    --ink-2: #30363d;
    --ink-3: #3d444c;
    --navy-text: #1d2a4a;
  }
  html, body {
    margin: 0;
    width: 1200px;
    height: 1200px;
    overflow: hidden;
    background: var(--stage);
    font-family: "Open Sans", Arial, sans-serif;
  }
  .deck { position: relative; width: 1200px; height: 1200px; }
  .slide {
    position: absolute;
    width: 475px;
    height: 268px;
    background: var(--paper);
  }
  .slide svg { display: block; width: 100%; height: 100%; }
  .col-left { left: 93px; }
  .col-right { left: 632px; }
  .row-1 { top: 140px; }
  .row-2 { top: 466px; }
  .row-3 { top: 793px; }

  .header-band { fill: var(--header-grey); }
  .pattern { fill: url(#royalPattern); }
  .slide-title { fill: var(--paper); font-weight: 700; font-size: 13px; letter-spacing: .2px; }
  .title-rule { stroke: var(--paper); stroke-width: 1.2; }
  .brand-name { fill: var(--navy-text); font-weight: 700; font-size: 8px; }
  .brand-name-small { fill: var(--navy-text); font-weight: 700; font-size: 7px; }
  .brand-mark { fill: var(--navy-text); }
  .site-url { fill: var(--navy-text); font-weight: 700; font-size: 7.5px; }
  .hero-text { fill: var(--paper); font-weight: 700; font-size: 12px; }
  .caption { fill: var(--ink-1); font-weight: 600; font-size: 5.4px; text-anchor: middle; }
  .step-shape-1 { fill: var(--ink-1); }
  .step-shape-2 { fill: var(--ink-2); }
  .step-shape-3 { fill: var(--ink-3); }
  .step-label { fill: var(--paper); font-size: 12.5px; text-anchor: middle; }
  .tile-label { fill: var(--paper); font-size: 10px; text-anchor: middle; }
  .icon { fill: var(--ink-1); }
  .icon-light { fill: var(--paper); }
  .royal { fill: var(--royal); }
  .band-heading { fill: var(--paper); font-size: 16px; }
  .band-copy { fill: var(--paper); font-weight: 700; font-size: 9.3px; }
  .col-heading { fill: var(--paper); font-weight: 600; font-size: 8px; }
  .col-copy { fill: var(--paper); font-weight: 600; font-size: 5px; }
  .body-copy { fill: var(--ink-1); font-weight: 600; font-size: 7.2px; }
  .option-letter { fill: var(--paper); font-size: 14px; text-anchor: middle; }
  .option-copy { fill: var(--paper); font-weight: 600; font-size: 4.4px; }
</style>
</head>
<body>
<div class="deck">
  <svg width="0" height="0" aria-hidden="true" style="position:absolute">
    <defs>
      <linearGradient id="royalPattern" x1="0" y1="0" x2="1" y2="1">
        <stop offset="0" stop-color="#0a0c9a"/>
        <stop offset=".5" stop-color="#1a3fae"/>
        <stop offset="1" stop-color="#0c0ea4"/>
      </linearGradient>
      <linearGradient id="groupPhoto" x1="0" y1="0" x2="1" y2="1">
        <stop offset="0" stop-color="#d9d2c8"/>
        <stop offset=".5" stop-color="#6d5a4c"/>
        <stop offset="1" stop-color="#3a302b"/>
      </linearGradient>
      <linearGradient id="portraitPhoto" x1="0" y1="0" x2="0" y2="1">
        <stop offset="0" stop-color="#ebe8e3"/>
        <stop offset="1" stop-color="#cdc4b8"/>
      </linearGradient>
      <radialGradient id="searchArt" cx=".5" cy=".4" r=".6">
        <stop offset="0" stop-color="#1a2fae"/>
        <stop offset=".6" stop-color="#2c3440"/>
        <stop offset="1" stop-color="#eef0f3"/>
      </radialGradient>
    </defs>
  </svg>

  <!-- Cover -->
  <section class="slide col-left row-1">
    <svg viewBox="0 0 440 248">
      <rect x="58" y="0" width="250" height="220" fill="url(#groupPhoto)" role="img" aria-label="Photo of a group of smiling students on a staircase"/>
      <polygon class="pattern" points="300,0 425,0 425,132 312,248 0,248 0,220 215,220 300,135" role="img" aria-label="Blue geometric triangle pattern"/>
      <rect class="royal" x="0" y="220" width="320" height="28"/>
      <rect class="brand-mark" x="15" y="12" width="8" height="8"/>
      <text class="brand-name" x="15" y="31">KORVA</text>
      <text class="brand-name" x="15" y="41">PATH</text>
      <text class="hero-text" x="240" y="158">KORVA PATH</text>
      <text class="hero-text" x="240" y="175">Universities</text>
      <text class="hero-text" x="240" y="192">Entrance Services</text>
    </svg>
  </section>

  <!-- Who we are -->
  <section class="slide col-right row-1">
    <svg viewBox="0 0 440 248">
      <rect class="header-band" x="0" y="0" width="395" height="40"/>
      <polygon class="pattern" points="250,0 395,0 345,52 234,52" role="img" aria-label="Blue geometric triangle pattern"/>
      <text class="slide-title" x="12" y="23">WHO WE ARE</text>
      <line class="title-rule" x1="12" y1="31" x2="120" y2="31"/>
      <rect class="brand-mark" x="388" y="20" width="7" height="7"/>
      <text class="brand-name-small" x="398" y="27">KORVA</text>
      <polygon class="step-shape-1" points="42,88 150,88 172,119 150,150 42,150 64,119"/>
      <polygon class="step-shape-2" points="156,88 264,88 286,119 264,150 156,150 178,119"/>
      <polygon class="step-shape-3" points="270,88 378,88 400,119 378,150 270,150 292,119"/>
      <text class="step-label" x="105" y="124">STEP 1</text>
      <text class="step-label" x="219" y="124">STEP 2</text>
      <text class="step-label" x="333" y="124">STEP 3</text>
      <g class="caption">
        <text x="106" y="171">Lorem ipsum dolor sit amet, enim</text>
        <text x="106" y="182">dolore mucius ei eam. Esse aliquip</text>
        <text x="106" y="193">nonumes et eos. Eripuit deserunt</text>
        <text x="106" y="204">argumentum id eum, nulla nonumes.</text>
        <text x="220" y="171">Lorem ipsum dolor sit amet, enim</text>
        <text x="220" y="182">dolore mucius ei eam. Esse aliquip</text>
        <text x="220" y="193">nonumes et eos. Eripuit deserunt</text>
        <text x="220" y="204">argumentum id eum, nulla nonumes.</text>
        <text x="334" y="171">Lorem ipsum dolor sit amet, enim</text>
        <text x="334" y="182">dolore mucius ei eam. Esse aliquip</text>
        <text x="334" y="193">nonumes et eos. Eripuit deserunt</text>
        <text x="334" y="204">argumentum id eum, nulla nonumes.</text>
      </g>
      <text class="site-url" x="17" y="234">www.korvapath.ae</text>
    </svg>
  </section>

  <!-- What we do -->
  <section class="slide col-left row-2">
    <svg viewBox="0 0 440 248">
      <rect class="header-band" x="0" y="0" width="395" height="40"/>
      <polygon class="pattern" points="290,0 395,0 345,52 234,52" role="img" aria-label="Blue geometric triangle pattern"/>
      <text class="slide-title" x="14" y="22">WHAT WE DO</text>
      <line class="title-rule" x1="14" y1="30" x2="120" y2="30"/>
      <rect class="brand-mark" x="388" y="24" width="7" height="7"/>
      <text class="brand-name-small" x="398" y="31">KORVA</text>
      <g class="icon">
        <rect x="82" y="84" width="2" height="8"/><rect x="85" y="80" width="2" height="12"/>
        <rect x="88" y="82" width="2" height="10"/><rect x="91" y="77" width="2" height="15"/>
        <rect x="94" y="81" width="2" height="11"/><rect x="80" y="92" width="18" height="1.2"/>
        <polygon points="220,73 208,83 211,83 211,93 218,93 218,87 222,87 222,93 229,93 229,83 232,83"/>
        <circle cx="347" cy="78" r="5"/>
        <path d="M338 93 q0 -10 9 -10 q9 0 9 10 z"/>
      </g>
      <rect class="step-shape-1" x="37" y="100" width="111" height="46"/>
      <rect class="step-shape-2" x="164" y="100" width="111" height="46"/>
      <rect class="step-shape-3" x="292" y="100" width="111" height="46"/>
      <text class="tile-label" x="92" y="126">Lorem ipsum</text>
      <text class="tile-label" x="220" y="126">Lorem ipsum</text>
      <text class="tile-label" x="347" y="126">Lorem ipsum</text>
      <g class="caption">
        <text x="92" y="165">Lorem ipsum dolor sit amet, enim</text>
        <text x="92" y="176">dolore mucius ei eam. Esse aliquip</text>
        <text x="92" y="187">nonumes et eos. Eripuit deserunt</text>
        <text x="92" y="198">argumentum id eum, nulla nonumes.</text>
        <text x="220" y="165">Lorem ipsum dolor sit amet, enim</text>
        <text x="220" y="176">dolore mucius ei eam. Esse aliquip</text>
        <text x="220" y="187">nonumes et eos. Eripuit deserunt</text>
        <text x="220" y="198">argumentum id eum, nulla nonumes.</text>
        <text x="347" y="165">Lorem ipsum dolor sit amet, enim</text>
        <text x="347" y="176">dolore mucius ei eam. Esse aliquip</text>
        <text x="347" y="187">nonumes et eos. Eripuit deserunt</text>
        <text x="347" y="198">argumentum id eum, nulla nonumes.</text>
      </g>
      <text class="site-url" x="17" y="238">www.korvapath.ae</text>
    </svg>
  </section>

  <!-- Education levels -->
  <section class="slide col-right row-2">
    <svg viewBox="0 0 440 248">
      <rect class="header-band" x="0" y="0" width="395" height="40"/>
      <polygon class="pattern" points="250,0 395,0 345,52 234,52" role="img" aria-label="Blue geometric triangle pattern"/>
      <text class="slide-title" x="14" y="22">EDUCATION LEVELS</text>
      <line class="title-rule" x1="14" y1="30" x2="120" y2="30"/>
      <rect class="brand-mark" x="388" y="24" width="7" height="7"/>
      <text class="brand-name-small" x="398" y="31">KORVA</text>
      <rect class="royal" x="0" y="80" width="440" height="116"/>
      <rect class="pattern" x="350" y="78" width="90" height="98" role="img" aria-label="Blue geometric triangle pattern"/>
      <rect x="246" y="58" width="104" height="158" fill="url(#portraitPhoto)" role="img" aria-label="Photo of a student in traditional white dress holding books"/>
      <text class="band-heading" x="22" y="108">Lorem ipsum</text>
      <text class="band-copy" x="22" y="126">Lorem ipsum dolor sit amet, enim</text>
      <text class="band-copy" x="22" y="145">dolore mucius ei eam. Esse aliquip</text>
      <text class="band-copy" x="22" y="163">nonumes et eos. Eripuit deserunt</text>
      <text class="band-copy" x="22" y="182">argumentum id eum, nulla nonumes.</text>
      <text class="site-url" x="17" y="234">www.korvapath.ae</text>
    </svg>
  </section>

  <!-- Why choose -->
  <section class="slide col-left row-3">
    <svg viewBox="0 0 440 248">
      <rect class="header-band" x="0" y="0" width="395" height="40"/>
      <polygon class="pattern" points="290,0 395,0 345,52 234,52" role="img" aria-label="Blue geometric triangle pattern"/>
      <text class="slide-title" x="14" y="24">WHY CHOOSE KORVA PATH</text>
      <line class="title-rule" x1="14" y1="32" x2="200" y2="32"/>
      <rect class="brand-mark" x="388" y="24" width="7" height="7"/>
      <text class="brand-name-small" x="398" y="31">KORVA</text>
      <rect class="royal" x="0" y="76" width="320" height="24"/>
      <text class="tile-label" x="248" y="92" style="font-size:11px">Lorem Ipsum</text>
      <rect class="step-shape-1" x="0" y="100" width="83" height="148"/>
      <rect class="step-shape-2" x="83" y="100" width="83" height="148"/>
      <rect class="step-shape-3" x="166" y="100" width="83" height="148"/>
      <g class="col-heading">
        <text x="10" y="121">Lorem ipsum</text>
        <text x="93" y="121">Lorem ipsum</text>
        <text x="176" y="121">Lorem ipsum</text>
      </g>
      <g class="col-copy">
        <text x="10" y="139">Lorem ipsum dolor sit</text><text x="10" y="148">amet, enim dolore mucius</text>
        <text x="10" y="157">ei eam. Esse aliquip</text><text x="10" y="166">nonumes et eos. Eripuit</text>
        <text x="10" y="175">deserunt argumentum id.</text><text x="10" y="187">Lorem ipsum dolor sit</text>
        <text x="10" y="196">amet, enim dolore mucius</text><text x="10" y="205">ei eam. Esse aliquip</text>
        <text x="10" y="214">nonumes et eos. Eripuit</text><text x="10" y="223">deserunt argumentum id.</text>
        <text x="93" y="139">Lorem ipsum dolor sit</text><text x="93" y="148">amet, enim dolore mucius</text>
        <text x="93" y="157">ei eam. Esse aliquip</text><text x="93" y="166">nonumes et eos. Eripuit</text>
        <text x="93" y="175">deserunt argumentum id.</text><text x="93" y="187">Lorem ipsum dolor sit</text>
        <text x="93" y="196">amet, enim dolore mucius</text><text x="93" y="205">ei eam. Esse aliquip</text>
        <text x="93" y="214">nonumes et eos. Eripuit</text><text x="93" y="223">deserunt argumentum id.</text>
        <text x="176" y="139">Lorem ipsum dolor sit</text><text x="176" y="148">amet, enim dolore mucius</text>
        <text x="176" y="157">ei eam. Esse aliquip</text><text x="176" y="166">nonumes et eos. Eripuit</text>
        <text x="176" y="175">deserunt argumentum id.</text><text x="176" y="187">Lorem ipsum dolor sit</text>
        <text x="176" y="196">amet, enim dolore mucius</text><text x="176" y="205">ei eam. Esse aliquip</text>
        <text x="176" y="214">nonumes et eos. Eripuit</text><text x="176" y="223">deserunt argumentum id.</text>
      </g>
      <rect x="322" y="72" width="92" height="136" fill="url(#searchArt)" role="img" aria-label="Illustration of a magnifying glass with a blue lens"/>
    </svg>
  </section>

  <!-- Study destination -->
  <section class="slide col-right row-3">
    <svg viewBox="0 0 440 248">
      <rect class="header-band" x="0" y="0" width="395" height="40"/>
      <polygon class="pattern" points="250,0 395,0 345,52 234,52" role="img" aria-label="Blue geometric triangle pattern"/>
      <text class="slide-title" x="14" y="22">STUDY DESTINATION</text>
      <line class="title-rule" x1="14" y1="30" x2="120" y2="30"/>
      <rect class="brand-mark" x="388" y="24" width="7" height="7"/>
      <text class="brand-name-small" x="398" y="31">KORVA</text>
      <rect class="step-shape-1" x="23" y="77" width="34" height="34"/>
      <rect class="step-shape-1" x="74" y="77" width="34" height="34"/>
      <rect class="step-shape-1" x="125" y="77" width="34" height="34"/>
      <g class="icon-light">
        <rect x="33" y="94" width="2" height="6"/><rect x="36" y="90" width="2" height="10"/>
        <rect x="39" y="92" width="2" height="8"/><rect x="42" y="88" width="2" height="12"/>
        <rect x="45" y="91" width="2" height="9"/><rect x="32" y="100" width="16" height="1"/>
        <polygon points="91,85 80,94 83,94 83,102 89,102 89,97 93,97 93,102 99,102 99,94 102,94"/>
        <circle cx="142" cy="89" r="4.5"/>
        <path d="M134 102 q0 -9 8 -9 q8 0 8 9 z"/>
      </g>
      <g class="body-copy">
        <text x="23" y="132">Lorem ipsum dolor sit amet, enim</text>
        <text x="23" y="145">dolore mucius ei eam. Esse aliquip</text>
        <text x="23" y="158">nonumes et eos. Eripuit deserunt</text>
        <text x="23" y="171">argumentum id eum, nulla nonumes.</text>
        <text x="23" y="184">Lorem ipsum dolor sit amet, enim</text>
        <text x="23" y="197">dolore mucius ei eam. Esse aliquip</text>
        <text x="23" y="210">nonumes et eos. Eripuit deserunt</text>
      </g>
      <rect class="step-shape-1" x="220" y="77" width="186" height="33"/>
      <rect class="step-shape-3" x="220" y="77" width="38" height="33"/>
      <rect class="step-shape-1" x="220" y="132" width="186" height="33"/>
      <rect class="step-shape-3" x="220" y="132" width="38" height="33"/>
      <rect class="step-shape-1" x="220" y="187" width="186" height="33"/>
      <rect class="step-shape-3" x="220" y="187" width="38" height="33"/>
      <text class="option-letter" x="239" y="99">A</text>
      <text class="option-letter" x="239" y="154">B</text>
      <text class="option-letter" x="239" y="209">C</text>
      <g class="option-copy">
        <text x="263" y="92">Lorem ipsum dolor sit amet, enim dolore mucius</text>
        <text x="263" y="98">ei eam. Esse aliquip nonumes et eos. Eripuit deserunt.</text>
        <text x="263" y="147">Lorem ipsum dolor sit amet, enim dolore mucius</text>
        <text x="263" y="153">ei eam. Esse aliquip nonumes et eos. Eripuit deserunt.</text>
        <text x="263" y="202">Lorem ipsum dolor sit amet, enim dolore mucius</text>
        <text x="263" y="208">ei eam. Esse aliquip nonumes et eos. Eripuit deserunt.</text>
      </g>
      <text class="site-url" x="17" y="236">www.korvapath.ae</text>
    </svg>
  </section>
</div>
</body>
</html>
```